Corvel Capital LLC

Need Professional Business cards for New Investment Fund

Target Market(s)

High Quality investors

Industry/Entity Type

Financial

Contact Information for Business Card

Phone Number +1 555 284 6190
Name Lukas Varenko
Title Fund Manager
email lv@FundCorvel.com
Website www.FundCorvel.com

Colors

Designer to choose colors to be used in the design.

Requirements
Must have
• Must have our Logo and all of the above. Must be made so lettering and loge can be raised

```html
<!DOCTYPE html>
<html lang="en">
<head>
<meta charset="utf-8">
<title>Corvel Capital LLC – Business Card</title>
<link href="https://fonts.googleapis.com/css2?family=Roboto:wght@400;500;700&display=swap" rel="stylesheet">
<style>
  :root {
    --backdrop: #3a3a3c;
    --card-black: #1c1c1e;
    --panel-grey: #3f4641;
    --lime: #8cc63f;
    --ink-light: #ffffff;
    --ink-soft: #e4e6e4;
    --emboss: #3a3a3d;
  }
  * { box-sizing: border-box; margin: 0; padding: 0; }
  html, body {
    width: 799px; height: 1200px; overflow: hidden;
    background: var(--backdrop);
    font-family: "Roboto", Arial, sans-serif;
  }
  .sheet {
    width: 799px; height: 1200px;
    display: flex; flex-direction: column; align-items: center; justify-content: space-evenly;
  }
  .card {
    position: relative;
    width: 680px; height: 389px;
    border-radius: 6px;
    overflow: hidden;
    background: var(--card-black);
  }
  /* Front */
  .card-front { display: flex; align-items: center; justify-content: center; }
  .front-brand {
    font-size: 44px; font-weight: 500; letter-spacing: 2px;
    color: var(--emboss);
  }
  /* Back */
  .accent-band {
    position: absolute; left: 0; right: 0; top: 150px; height: 50px;
    background: linear-gradient(180deg, var(--card-black) 0%, #2f3a26 55%, var(--panel-grey) 100%);
  }
  .lower-panel {
    position: absolute; left: 0; right: 0; top: 200px; bottom: 0;
    background: var(--panel-grey);
  }
  .back-brand {
    position: absolute; left: 44px; top: 48px;
    display: flex; align-items: center; gap: 10px;
    font-size: 22px; font-weight: 500; color: var(--ink-light);
  }
  .back-brand .brand-dot {
    width: 14px; height: 14px; background: var(--lime);
  }
  .address {
    position: absolute; left: 40px; top: 240px;
    font-size: 15px; line-height: 22px; color: var(--ink-soft);
    font-style: normal;
  }
  .contact {
    position: absolute; right: 36px; top: 222px;
    text-align: right; color: var(--ink-light);
  }
  .contact .person-name { font-size: 25px; font-weight: 700; line-height: 30px; }
  .contact .person-title { font-size: 15px; color: var(--ink-soft); margin: 3px 0 12px; }
  .contact-line {
    display: flex; align-items: center; justify-content: flex-end; gap: 9px;
    font-size: 16px; line-height: 23px;
  }
  .contact-line svg { width: 15px; height: 15px; fill: var(--ink-light); flex: none; }
</style>
</head>
<body>
<main class="sheet">
  <section class="card card-front" aria-label="Card front">
    <span class="front-brand">Corvel Capital LLC</span>
  </section>

  <section class="card card-back" aria-label="Card back">
    <div class="accent-band" role="img" aria-label="Decorative lime-green wave accent dividing the card"></div>
    <div class="lower-panel"></div>

    <div class="back-brand"><span class="brand-dot"></span>Corvel Capital LLC</div>

    <address class="address">
      48 Alder Row,<br>Fairhaven, NJ, 07990
    </address>

    <div class="contact">
      <div class="person-name">Lukas Varenko</div>
      <div class="person-title">Fund Manager</div>
      <div class="contact-line">+1 555 284 6190
        <svg viewBox="0 0 24 24" aria-hidden="true"><path d="M6.6 10.8a15 15 0 0 0 6.6 6.6l2.2-2.2a1 1 0 0 1 1-.25 11.4 11.4 0 0 0 3.6.6 1 1 0 0 1 1 1V20a1 1 0 0 1-1 1A17 17 0 0 1 3 4a1 1 0 0 1 1-1h3.5a1 1 0 0 1 1 1c0 1.25.2 2.45.6 3.6a1 1 0 0 1-.25 1z"/></svg>
      </div>
      <div class="contact-line">lv@FundCorvel.com
        <svg viewBox="0 0 24 24" aria-hidden="true"><path d="M2 5h20v14H2z M4 7v.5l8 5 8-5V7l-8 5z" fill-rule="evenodd"/></svg>
      </div>
      <div class="contact-line">www.FundCorvel.com
        <svg viewBox="0 0 24 24" aria-hidden="true"><path d="M12 2a10 10 0 1 0 0 20 10 10 0 0 0 0-20zm6.9 6h-2.9a15 15 0 0 0-1.4-3.6A8 8 0 0 1 18.9 8zM12 4c.8 1.2 1.5 2.5 1.9 4h-3.8c.4-1.5 1.1-2.8 1.9-4zM4.3 14a8 8 0 0 1 0-4h3.4a16 16 0 0 0 0 4zm.8 2h2.9c.3 1.3.8 2.5 1.4 3.6A8 8 0 0 1 5.1 16zM8 8H5.1a8 8 0 0 1 4.3-3.6C8.8 5.5 8.3 6.7 8 8zm4 12c-.8-1.2-1.5-2.5-1.9-4h3.8c-.4 1.5-1.1 2.8-1.9 4zm2.3-6H9.7a14 14 0 0 1 0-4h4.6a14 14 0 0 1 0 4zm.3 5.6c.6-1.1 1.1-2.3 1.4-3.6h2.9a8 8 0 0 1-4.3 3.6zm1.7-5.6a16 16 0 0 0 0-4h3.4a8 8 0 0 1 0 4z"/></svg>
      </div>
    </div>
  </section>
</main>
</body>
</html>
```